High-End Print/Digital Ad for Unique Luxury Travel Company Required

Objective:
Design a compelling and visually striking advertisement that highlights our company’s unmatched luxury travel experiences. The ad should elevate our brand image, spark curiosity, and drive prospective clients to contact us.
Target Audience:
• Affluent individuals seeking extraordinary, tailor-made travel experiences
• Affluent, luxury, high-net-worth individuals looking for value, expertise, and white-glove service
• Professionals or retirees who appreciate unique, thoughtfully curated travel over mainstream tourism
Key Messages to Communicate:
• One-of-a-kind luxury travel: Once-in-a-lifetime experiences that are curated with creativity and meticulous attention to detail
• Exceptional service: White-glove, personalized planning from start to finish
• 38 years’ travel experience – expert knowledge of destinations, modes of travel, premium accommodations and well-established, meaningful industry connections.
• Highly trusted: Cruise line executives often say, “No one does what you do.”
Tone and Style:
• Elegant, luxurious, sophisticated
• Eye-catching, polished, and modern
• Professional but warm—conveys trust and credibility
• High-impact visuals (full-bleed imagery, custom graphics, or high-end photography)
Deliverables:
• One full-page print ad and digital ad
• Ready-to-print, high-resolution file + working file (PSD, AI, etc.)
Optional: Social media-optimized version or short motion-graphic variation (if designer offers it)
Inspiration & Visual Style Suggestions:
• Think Lumen Voyages, Harrow Pike Wanderer, Silver Quill, or Orvel Retreats ad styles
• Large, emotive imagery with elegant typography
• Clean layout that speaks luxury, clarity, and trust
Copy Direction (draft):
For those who’ve explored the world—and crave something beyond the ordinary.
Each journey is a masterfully curated experience, rich in detail, seamless in execution, and unforgettable in every way.
Founded in 1997, Tidewell Journeys is a unique travel company specializing in cruising, all-inclusive luxury properties, and tours world-wide for individuals, groups, and incentives.
We offer an exceptional range of services designed to ensure every journey is flawlessly executed and truly unforgettable.
Let us help you plan your next extraordinary adventure.
Note: You may refine the copy slightly based on layout or format needs.
Other Resources for References:
1. Website - www.tidewelljourneys-example.com

```html
<!DOCTYPE html>
<html lang="en">
<head>
<meta charset="utf-8">
<title>Tidewell Journeys – Full-Page Ad</title>
<link rel="stylesheet" href="https://fonts.googleapis.com/css2?family=Cinzel:wght@400;600;700&family=Figtree:wght@400;500&display=swap">
<style>
  :root {
    --backdrop: #cdc8c4;
    --navy-deep: #0a1a44;
    --navy-mid: #1b3878;
    --navy-sky: #2a4f97;
    --snow: #e6e9ed;
    --snow-shade: #b9bfc8;
    --rock: #6f747c;
    --crimson: #a61d25;
    --band-indigo: #262a75;
    --band-violet: #333b94;
    --gold: #e2d57f;
    --ink: #1b1b1b;
    --white: #ffffff;
    --paper: #ffffff;
  }
  * { margin: 0; padding: 0; box-sizing: border-box; }
  html, body {
    width: 774px;
    height: 1200px;
    overflow: hidden;
    background: var(--backdrop);
  }
  .ad {
    position: absolute;
    left: 17px;
    top: 121px;
    width: 740px;
    height: 958px;
    overflow: hidden;
    background: linear-gradient(180deg, var(--navy-deep) 0%, var(--navy-mid) 40%, var(--navy-sky) 75%);
    box-shadow: 0 6px 14px rgba(0,0,0,0.25);
    font-family: "Figtree", sans-serif;
    color: var(--white);
  }
  .hero-photo {
    position: absolute;
    left: 0;
    top: 256px;
    width: 740px;
    height: 547px;
    background:
      radial-gradient(ellipse 300px 420px at 215px 400px, rgba(232,236,241,0.97) 0%, rgba(176,183,194,0.9) 42%, rgba(111,116,124,0.55) 62%, rgba(42,79,151,0) 80%),
      radial-gradient(ellipse 300px 300px at 760px 470px, rgba(226,230,235,0.95) 0%, rgba(150,156,166,0.75) 50%, rgba(42,79,151,0) 78%),
      linear-gradient(180deg, rgba(42,79,151,0) 0%, rgba(42,79,151,0) 52%, rgba(120,126,136,0.85) 68%, var(--snow-shade) 82%, var(--snow) 100%);
  }
  .headline {
    position: absolute;
    left: 0;
    top: 50px;
    width: 740px;
    text-align: center;
    font-family: "Cinzel", serif;
    font-weight: 700;
    font-size: 45.5px;
    line-height: 42px;
    letter-spacing: 0.5px;
  }
  .lede {
    position: absolute;
    left: 235px;
    top: 240px;
    width: 440px;
    text-align: center;
    font-size: 19px;
    line-height: 21px;
  }
  .founding {
    position: absolute;
    left: 424px;
    top: 354px;
    width: 310px;
  }
  .founding__rule {
    position: absolute;
    left: 0;
    top: 12px;
    height: 122px;
    border-left: 1.5px dotted rgba(255,255,255,0.8);
  }
  .founding__rule::before {
    content: "";
    position: absolute;
    left: -3px;
    top: -6px;
    width: 4.5px;
    height: 4.5px;
    border-radius: 50%;
    background: var(--gold);
  }
  .founding__title {
    margin-left: 16px;
    font-family: "Cinzel", serif;
    font-weight: 600;
    font-size: 25.5px;
    line-height: 30px;
    color: var(--gold);
  }
  .founding__body {
    margin-left: 16px;
    margin-top: 1px;
    font-size: 16px;
    line-height: 20px;
  }
  .services {
    position: absolute;
    left: 0;
    top: 661px;
    width: 427px;
    height: 142px;
    background: var(--crimson);
    padding: 20px 0 0 63px;
    font-size: 22px;
    font-weight: 500;
    line-height: 24.3px;
  }
  .cta-band {
    position: absolute;
    left: 0;
    top: 803px;
    width: 740px;
    height: 59px;
    background: linear-gradient(90deg, var(--band-indigo), var(--band-violet) 60%, var(--band-indigo));
    display: flex;
    align-items: center;
    justify-content: center;
    font-family: "Cinzel", serif;
    font-weight: 600;
    font-size: 18.4px;
    letter-spacing: 0.3px;
  }
  .web-footer {
    position: absolute;
    left: 0;
    top: 862px;
    width: 740px;
    height: 96px;
    background: var(--paper);
    display: flex;
    align-items: center;
    justify-content: center;
    font-family: "Cinzel", serif;
    font-weight: 700;
    font-size: 22px;
    color: var(--ink);
    letter-spacing: 0.3px;
  }
</style>
</head>
<body>
  <main class="ad">
    <div class="hero-photo" role="img" aria-label="Photograph of a snow-covered Himalayan peak rising into a deep blue sky above a snowy rocky slope"></div>

    <h1 class="headline">For those who’ve<br>explored the world and<br>crave something<br>beyond the ordinary.</h1>

    <p class="lede">Each journey is a masterfully curated experience,<br>rich in detail, seamless in execution,<br>and unforgettable in every way.</p>

    <section class="founding">
      <span class="founding__rule"></span>
      <h2 class="founding__title">Founded in 1997,</h2>
      <p class="founding__body">Tidewell Journeys is a unique travel<br>company specializing in cruising,<br>all-inclusive luxury properties, and<br>tours world-wide for individuals,<br>groups, and incentives.</p>
    </section>

    <p class="services">We offer an exceptional range<br>of services designed to ensure<br>every journey is flawlessly<br>executed and truly unforgettable.</p>

    <p class="cta-band">Let us help you plan your next extraordinary adventure.</p>

    <p class="web-footer">WWW.TIDEWELLJOURNEYS-EXAMPLE.COM</p>
  </main>
</body>
</html>
```